Label and packaging - Lune de Sable

We are after label and pack design for a product called Lune de Sable. This product is a blend of Pinot Gris and Apple Cider.

Lune de Sable:

The packaging needs to accomplish the following: quickly explain what the product is, establish as a premium price product and grab the eye. The package should also reflect the product innovation.

Quickly Explain What the Product Is:

Lune de Sable is a nice name that could lift the image – but no one will have any idea what the product is by the name. Consider that a consumer will be staring at a shelf, then the bottle for maybe two to three seconds before moving on to another bottle. In those three seconds we need to make certain that they understand that the product is a blend of wine and cider. Lune de Sable will not support this on its own.

Suggestion is to use words like Wine, Cider, Orchard, Vine, Apple, Heirloom, Exotic and make it simple. Perhaps a sticker that says “50% Wine/50% Apple Cider” that sits on the neck of every bottle. They need to quickly ‘get it”. Imagery will assist as well. Consider a hybrid 50/50 image of wine grapes and apples to tell the story.

Establish a Premium Price Point:

The label needs to say high quality in the package and the font. Have fun with the shipper – this is where you can have a field day with imagery and fun buzz words – we love the idea of a busy shipper that tells the story with a clean and smart looking bottle.

Target Market(s)

This is a premium product targeted at females of age 25-45.

Industry/Entity Type

Consumer

Colors
ec1f27
9bcb3c

Requirements
Must have
• Label design on a burgundy bottle with a screw cap, see here for bottle shape: http://www.vk-flaskrange.co.nz/wine/#/?view=thumbs&segments=41&colors=&capacityMin=187&capacityMax=750&heightMin=171&heightMax=334&labelMin=44&labelMax=168&neckMin=0&neckMax=1000

Packaging design on a 12 x 750ml carton. This sort of thing: https://www.barrelnook.com.au/images/photo06.jpg

Nice to have
• We have attached some examples of a concept we quite like but it's not bright enough.

```html
<!DOCTYPE html>
<html lang="en">
<head>
<meta charset="utf-8">
<title>Lune de Sable – Label</title>
<link rel="stylesheet" href="https://fonts.googleapis.com/css2?family=Arimo:wght@400;700&family=Caveat+Brush&display=swap">
<style>
  :root {
    --page: #ffffff;
    --label-cream: #f3e6c6;
    --label-light: #fbf5e6;
    --ink: #1d1a16;
    --apple-red: #ec1f27;
    --apple-warm: #f06a2a;
    --grape-green: #9bcb3c;
    --grape-pale: #d9ec9a;
    --bar: #0d0c0a;
  }
  * { box-sizing: border-box; margin: 0; padding: 0; }
  html, body {
    width: 1200px;
    height: 1115px;
    overflow: hidden;
    background: var(--page);
  }
  .canvas {
    position: relative;
    width: 1200px;
    height: 1115px;
  }
  .label {
    position: absolute;
    left: 338px;
    top: 107px;
    width: 524px;
    height: 900px;
    background: linear-gradient(160deg, var(--label-light) 0%, var(--label-cream) 55%, #ecdcb4 100%);
    font-family: "Arimo", Arial, sans-serif;
    color: var(--ink);
    overflow: hidden;
  }
  .label__artwork {
    position: absolute;
    left: 0;
    top: 89px;
    width: 524px;
    height: 507px;
  }
  .label__brand {
    position: absolute;
    left: 0;
    right: 0;
    top: 290px;
    text-align: center;
    font-family: "Caveat Brush", cursive;
    font-weight: 400;
    font-size: 96px;
    line-height: 1;
    color: var(--ink);
    white-space: nowrap;
  }
  .label__vintage {
    position: absolute;
    left: 0;
    right: 0;
    top: 640px;
    text-align: center;
    font-weight: 400;
    font-size: 29px;
  }
  .label__blend {
    position: absolute;
    left: 0;
    right: 0;
    top: 690px;
    text-align: center;
    font-weight: 700;
    font-size: 19px;
    line-height: 35px;
    letter-spacing: 0.5px;
  }
  .label__bar {
    position: absolute;
    left: 0;
    right: 0;
    top: 770px;
    height: 38px;
    background: var(--bar);
  }
  .label__facts {
    position: absolute;
    left: 0;
    right: 0;
    top: 848px;
    display: flex;
    justify-content: center;
    gap: 92px;
    font-weight: 700;
    font-size: 18px;
    letter-spacing: 0.5px;
  }
</style>
</head>
<body>
  <main class="canvas">
    <section class="label">
      <svg class="label__artwork" viewBox="0 0 524 507" role="img" aria-label="Painted illustration of a red apple with a leaf beside a bunch of pale green grapes over white brush strokes">
        <defs>
          <linearGradient id="fruit-tones" x1="0" y1="0" x2="1" y2="1">
            <stop offset="0" stop-color="var(--apple-warm)" stop-opacity="0.85"/>
            <stop offset="0.35" stop-color="var(--apple-red)" stop-opacity="0.75"/>
            <stop offset="0.65" stop-color="var(--grape-pale)" stop-opacity="0.85"/>
            <stop offset="1" stop-color="var(--grape-green)" stop-opacity="0.8"/>
          </linearGradient>
        </defs>
        <rect x="0" y="0" width="524" height="507" fill="url(#fruit-tones)"/>
      </svg>
      <h1 class="label__brand">Lune de Sable</h1>
      <p class="label__vintage">2011</p>
      <p class="label__blend">BLEND OF APPLE CIDER<br>&amp; PINOT GRIS</p>
      <div class="label__bar"></div>
      <p class="label__facts"><span>750 ML</span><span>14,7%VOL</span></p>
    </section>
  </main>
</body>
</html>
```